Freelancer Information Security professional needs a business card

I need a simple, young, elegant business card. I'm a freelancer in the InfoSec area and want to be able to give my card to potential customers and new people I meet.

I'd like to have a clean, professional look but at same time not boring or corporate.

The only requirement is to have my "introduction" phrase which is:
"Half hacker, half mercenary."

I have added a card I have as a example, which I think it gives a good example of style I want.

Target Market(s)

Technology / Computers / Engineering

Industry/Entity Type

Information Technology

Contact Information for Business Card

Contact fields I want included:

(351) 93 618 20 54
tomas@vendoza.im
https://vendoza.im

Font styles to use
Sans Serif

Requirements
Nice to have
• Card doesn't need to have a doubled side, but it looks good / fits the design then please do include.
Should not have
• Outdated graphics or images; too much patterns/colors.

```html
<!DOCTYPE html>
<html lang="en">
<head>
<meta charset="utf-8">
<title>Tomas – Business Card</title>
<link rel="stylesheet" href="https://fonts.googleapis.com/css2?family=Roboto+Condensed:wght@300;400;700&display=swap">
<style>
  :root {
    --backdrop: #eceeee;
    --card: #ffffff;
    --blue: #00a0e3;
    --green: #94c12a;
    --ink: #333333;
    --icon-ink: #2a2a2a;
    --accent-soft: #cfeaf7;
  }
  * { margin: 0; padding: 0; box-sizing: border-box; }
  html, body {
    width: 1200px; height: 828px; overflow: hidden;
    background: var(--backdrop);
    font-family: "Roboto Condensed", sans-serif;
  }
  .card {
    position: absolute; left: 166px; top: 148px;
    width: 865px; height: 511px;
    background: var(--card);
    overflow: hidden;
    box-shadow: 0 6px 14px rgba(0,0,0,0.18);
  }
  .corner-art {
    position: absolute; left: 571px; top: 0;
    width: 294px; height: 341px;
    background: radial-gradient(ellipse at 55% 45%, var(--accent-soft) 0%, rgba(207,234,247,0.55) 45%, rgba(255,255,255,0) 75%);
  }
  .bar { position: absolute; left: 0; height: 50px; }
  .bar--blue { background: var(--blue); }
  .bar--green { background: var(--green); }
  .badge {
    position: absolute; width: 66px; height: 66px; margin: -33px 0 0 -33px;
    border-radius: 50%; background: var(--card);
    display: flex; align-items: center; justify-content: center;
  }
  .badge__disc {
    width: 54px; height: 54px; border-radius: 50%;
    display: flex; align-items: center; justify-content: center;
  }
  .badge__disc--blue { background: var(--blue); }
  .badge__disc--green { background: var(--green); }
  .badge__disc svg { width: 32px; height: 32px; }
  .name {
    position: absolute; left: 264px; top: 98px;
    font-weight: 700; font-size: 47px; letter-spacing: 1px;
    color: var(--blue); line-height: 52px;
  }
  .tagline {
    position: absolute; left: 53px; top: 164px;
    font-weight: 400; font-size: 28px; color: var(--blue);
    line-height: 32px; text-transform: uppercase; letter-spacing: -0.6px;
  }
  .contact {
    position: absolute; font-weight: 300; color: var(--ink);
    line-height: 36px;
  }
  .contact--phone { left: 282px; top: 245px; font-size: 32px; letter-spacing: 0.5px; }
  .contact--mail { left: 298px; top: 313px; font-size: 27.5px; }
  .contact--web { left: 306px; top: 380px; font-size: 26.5px; }
</style>
</head>
<body>
<div class="card">
  <div class="corner-art" role="img" aria-label="Decorative network illustration in light blue"></div>

  <div class="bar bar--blue" style="top:101px;width:224px"></div>
  <div class="badge" style="left:224px;top:126px">
    <div class="badge__disc badge__disc--blue" role="img" aria-label="Profile avatar"></div>
  </div>
  <div class="name">TOMAS</div>
  <div class="tagline">Half hacker, half mercenary</div>

  <div class="bar bar--green" style="top:238px;width:239px"></div>
  <div class="badge" style="left:239px;top:263px">
    <div class="badge__disc badge__disc--green">
      <svg viewBox="0 0 32 32" fill="none" stroke="var(--icon-ink)" stroke-width="2.2">
        <rect x="8" y="4" width="16" height="24" rx="2"/>
        <line x1="14" y1="24" x2="18" y2="24"/>
      </svg>
    </div>
  </div>
  <div class="contact contact--phone">(351) 93 618 20 54</div>

  <div class="bar bar--blue" style="top:304px;width:248px"></div>
  <div class="badge" style="left:248px;top:329px">
    <div class="badge__disc badge__disc--blue">
      <svg viewBox="0 0 32 32" fill="none" stroke="var(--icon-ink)" stroke-width="2.2">
        <rect x="3" y="8" width="26" height="17" rx="1.5"/>
        <polyline points="3,8 16,18 29,8"/>
      </svg>
    </div>
  </div>
  <div class="contact contact--mail">tomas@vendoza.im</div>

  <div class="bar bar--green" style="top:370px;width:257px"></div>
  <div class="badge" style="left:257px;top:396px">
    <div class="badge__disc badge__disc--green">
      <svg viewBox="0 0 32 32" fill="none" stroke="var(--icon-ink)" stroke-width="2">
        <circle cx="16" cy="16" r="12"/>
        <ellipse cx="16" cy="16" rx="5" ry="12"/>
        <line x1="4" y1="16" x2="28" y2="16"/>
        <line x1="16" y1="4" x2="16" y2="28"/>
        <path d="M6,10 H26 M6,22 H26"/>
      </svg>
    </div>
  </div>
  <div class="contact contact--web">https://vendoza.im</div>
</div>
</body>
</html>
```